Breakfast Cafe - The Sunny Nook

It is for my breakfast and lunch cafe with a hawaiian / beach theme. I am open 7 days a week from 7am to 2pm. We serve traditional American food such as omelettes, pancakes, burgers and sandwiches. I'll upload my old card and my new logo to be used. We have a lot of day to day regulars who eat there during the week, our t-shirts actually say 'Locals Only' on them. Hope this helps. Thanks.

Target Market(s)

anyone who has an appetite!

Industry/Entity Type

American Restaurant

Contact Information for Business Card

4815C Marlow Grove Avenue
Long Beach, California
(555) 731-2294

Requirements
Must have
• Address and phone number easily readable.
Nice to have
• beach or tropical theme

```html
<!DOCTYPE html>
<html lang="en">
<head>
<meta charset="utf-8">
<title>The Sunny Nook – Business Card</title>
<link href="https://fonts.googleapis.com/css2?family=Bebas+Neue&display=swap" rel="stylesheet">
<style>
  :root {
    --backdrop: #7a5638;
    --linen-light: #f3ead6;
    --linen-dark: #e6d6b6;
    --ink: #1b1c1e;
    --wave-yellow: #f4c21d;
    --wave-orange: #d9851a;
    --white: #ffffff;
    --orange: #f3a73a;
    --sky: #5cc3df;
    --brand: #2fa9cf;
    --badge-a: #f6b444;
    --badge-b: #c9792a;
  }
  * { margin: 0; padding: 0; box-sizing: border-box; }
  html, body {
    width: 1200px;
    height: 960px;
    overflow: hidden;
    background: var(--backdrop);
  }
  .card {
    position: absolute;
    left: 300px;
    top: 310px;
    width: 600px;
    height: 342px;
    border-radius: 22px;
    overflow: hidden;
    background: radial-gradient(ellipse at 60% 30%, var(--linen-light), var(--linen-dark));
    box-shadow: 0 6px 14px rgba(0, 0, 0, 0.35);
    font-family: "Bebas Neue", "Arial Narrow", sans-serif;
  }
  .card__wave {
    position: absolute;
    inset: 0;
    width: 600px;
    height: 342px;
  }
  .brand {
    position: absolute;
    left: 357px;
    top: 34px;
    width: 200px;
    text-align: center;
  }
  .brand__badge {
    display: block;
    width: 150px;
    height: 150px;
    margin: 0 auto;
    border-radius: 50%;
    background: radial-gradient(circle at 50% 40%, var(--badge-a), var(--badge-b));
  }
  .brand__name {
    display: block;
    margin-top: 4px;
    font-size: 36px;
    line-height: 1;
    color: var(--brand);
    letter-spacing: 1px;
  }
  .contact {
    position: absolute;
    left: 27px;
    top: 163px;
    color: var(--white);
  }
  .contact__phone {
    font-size: 28px;
    line-height: 1;
    letter-spacing: 0.5px;
  }
  .contact__address {
    margin-top: 14px;
    margin-left: 3px;
    font-size: 21px;
    line-height: 27px;
    font-style: normal;
  }
  .contact__tagline {
    margin-top: 14px;
    margin-left: 3px;
    font-size: 23px;
    line-height: 1;
    color: var(--orange);
  }
  .contact__hours {
    margin-top: 4px;
    margin-left: 3px;
    font-size: 17px;
    line-height: 1;
    color: var(--sky);
    letter-spacing: 0.3px;
  }
</style>
</head>
<body>
  <div class="card">
    <svg class="card__wave" viewBox="0 0 600 342" aria-hidden="true">
      <defs>
        <linearGradient id="wave-edge" x1="0" y1="0" x2="0" y2="1">
          <stop offset="0" stop-color="var(--wave-yellow)"/>
          <stop offset="1" stop-color="var(--wave-orange)"/>
        </linearGradient>
      </defs>
      <path d="M0,128 C70,85 160,85 230,125 C320,180 380,258 470,258 C530,258 570,222 600,182 L600,342 L0,342 Z" fill="url(#wave-edge)"/>
      <path d="M0,128 C70,85 160,85 230,130 C320,190 380,275 470,275 C530,275 570,245 600,212 L600,342 L0,342 Z" fill="var(--ink)"/>
    </svg>

    <div class="brand">
      <span class="brand__badge" role="img" aria-label="Round badge area for the cafe emblem"></span>
      <span class="brand__name">The Sunny Nook</span>
    </div>

    <div class="contact">
      <p class="contact__phone">P.(555) 731-2294</p>
      <address class="contact__address">
        4815C Marlow Grove Avenue<br>
        Long Beach, California
      </address>
      <p class="contact__tagline">Breakfast &amp; Lunch Cafe</p>
      <p class="contact__hours">Open 7 days a week from 7am to 2pm.</p>
    </div>
  </div>
</body>
</html>
```